Business Card Re-Design/Update

We'd like to update out business cards. I've included our current "Style guide" which has the colour scheme of the organisation in it. I've also included the branding files with logos etc in them.

I've also included a copy of one of our existing cards so that you can see how ugly/dated they look. I'd like a fresh modern corporate look.

Target Market(s)

These are for our clients, potential clients, industry contacts - like all business cards

Contact Information for Business Card

Name
Position
Company Address - Level 1, 47 Fernby Street, Carlow Qld 4072
Direct Phone
mobile
Email
Website -www.korvalit.com.au
Logo

Colors

Designer to choose colors to be used in the design.

Requirements
Must have
• Main Logo
• Cards will need to be editable to be able to personalize them for each new employee.
Nice to have
• The MapOut, ShipWell, KeepSteady would be okay to have if they can be sensibly and professionally added to the look without detracting from the main imagery.
• Maybe they could go on the back of the card? will leave this to your creative discretion as to whether/where they fit.
Should not have
• Should not have decorative or script fonts

```html
<!DOCTYPE html>
<html lang="en">
<head>
<meta charset="utf-8">
<title>KorvalIT Business Card</title>
<link href="https://fonts.googleapis.com/css2?family=Arimo:wght@400;700&display=swap" rel="stylesheet">
<style>
  :root {
    --brand-red: #d71920;
    --brand-red-deep: #b8141a;
    --ink-dark: #333538;
    --ink-mid: #3d3d3d;
    --paper: #ffffff;
    --backdrop: #eceae6;
    --ship-blue: #1b8fd2;
    --map-green: #5fae3c;
    --keep-purple: #b5288f;
  }
  * { margin: 0; padding: 0; box-sizing: border-box; }
  html, body { width: 1200px; height: 900px; overflow: hidden; }
  body {
    background: var(--backdrop);
    font-family: "Arimo", Arial, sans-serif;
    position: relative;
  }
  .card {
    position: absolute;
    left: 290px;
    width: 620px;
    height: 378px;
    overflow: hidden;
    box-shadow: 0 6px 18px rgba(0,0,0,0.18);
  }
  /* Front */
  .card-front { top: 48px; background: var(--brand-red); }
  .front-brand {
    position: absolute;
    top: 118px; left: 0; right: 0;
    display: flex; justify-content: center; align-items: center; gap: 18px;
    color: var(--paper);
    font-weight: 700;
    font-size: 50px;
    letter-spacing: -0.5px;
  }
  .brand-square { display: inline-block; width: 40px; height: 40px; background: var(--paper); }
  .service-band {
    position: absolute;
    top: 232px; left: 0; right: 0; height: 78px;
    background: var(--paper);
    display: flex; justify-content: center; align-items: center; gap: 26px;
  }
  .service {
    display: flex; align-items: center; gap: 8px;
    font-weight: 700; font-size: 24px;
  }
  .service-square { width: 20px; height: 20px; }
  .service-ship { color: var(--ship-blue); }
  .service-ship .service-square { background: var(--ship-blue); }
  .service-map { color: var(--map-green); }
  .service-map .service-square { background: var(--map-green); }
  .service-keep { color: var(--keep-purple); }
  .service-keep .service-square { background: var(--keep-purple); }

  /* Back */
  .card-back { top: 474px; background: var(--paper); }
  .decor-band {
    position: absolute;
    left: 0; right: 0; bottom: 0; height: 92px;
    background: linear-gradient(100deg, var(--ink-dark) 0%, var(--brand-red-deep) 35%, var(--brand-red) 100%);
  }
  .person { position: absolute; left: 36px; top: 36px; }
  .person-name {
    color: var(--brand-red); font-weight: 700; font-size: 23px;
    letter-spacing: 0.3px; text-transform: uppercase; line-height: 1;
  }
  .person-role { color: var(--ink-mid); font-size: 16px; margin-top: 3px; }
  .back-brand {
    position: absolute; right: 40px; top: 46px;
    display: flex; flex-direction: column; align-items: center; gap: 12px;
    color: var(--ink-dark); font-weight: 700; font-size: 40px; letter-spacing: -0.5px;
  }
  .back-brand .brand-square { width: 38px; height: 38px; background: var(--brand-red); }
  .contact-list { position: absolute; left: 36px; top: 126px; list-style: none; }
  .contact-list li {
    display: flex; align-items: center; gap: 9px;
    color: var(--ink-mid); font-size: 16px; line-height: 21px;
  }
  .contact-icon { width: 13px; height: 13px; fill: var(--brand-red); flex: none; }
  .address {
    position: absolute; left: 36px; top: 222px;
    color: var(--ink-mid); font-size: 16px; line-height: 21px; font-style: normal;
  }
  .website {
    position: absolute; right: 30px; bottom: 36px;
    color: var(--paper); font-size: 14px;
  }
</style>
</head>
<body>

<section class="card card-front" aria-label="Card front">
  <div class="front-brand"><span class="brand-square"></span>KorvalIT</div>
  <div class="service-band">
    <span class="service service-ship"><span class="service-square"></span>ShipWell</span>
    <span class="service service-map"><span class="service-square"></span>MapOut</span>
    <span class="service service-keep"><span class="service-square"></span>KeepSteady</span>
  </div>
</section>

<section class="card card-back" aria-label="Card back">
  <div class="decor-band" role="img" aria-label="Red and charcoal wave decoration along the lower edge"></div>

  <div class="person">
    <div class="person-name">Maren Holt</div>
    <div class="person-role">Business Development Manager</div>
  </div>

  <div class="back-brand"><span class="brand-square"></span>KorvalIT</div>

  <ul class="contact-list">
    <li><svg class="contact-icon" viewBox="0 0 14 14"><path d="M1,4 C1,2 3,1 7,1 C11,1 13,2 13,4 L10,5 L9,3.5 L5,3.5 L4,5 Z M3,7 L11,7 L12,13 L2,13 Z"/></svg>+61 (0)412 604 318</li>
    <li><svg class="contact-icon" viewBox="0 0 14 14"><path d="M3,0 H11 V14 H3 Z M4.5,2 V11 H9.5 V2 Z"/></svg>+61 (0)7 3184 2270</li>
    <li><svg class="contact-icon" viewBox="0 0 14 14"><path d="M3,0 H10 V4 H3 Z M0,5 H14 V11 H11 V14 H3 V11 H0 Z M4.5,9 V12.5 H9.5 V9 Z"/></svg>+61 (0)7 3184 2271</li>
    <li><svg class="contact-icon" viewBox="0 0 14 14"><path d="M0,2 H14 V12 H0 Z M1.5,3.5 L7,8 L12.5,3.5 Z" fill-rule="evenodd"/></svg>mholt@korvalit.com.au</li>
  </ul>

  <address class="address">Level 1, 47 Fernby Street<br>Carlow Qld 4072</address>

  <div class="website">www.korvalit.com.au</div>
</section>

</body>
</html>
```